Website Re-design and extension of an existing website

I have a Wordpress website currently and I need it to be upgraded. I have MOST of the content to get it started and the rest (video's, pictures ect) are on the way. I want to know if it is possible to convert my existing website into a Personal Brand website with a public speaking emphasis. I would like to have my website modeled after the following website:

http://www.vokalmira.com/

I have attached a document entitled "Website Outline & Content" that has all of the text on it and it has red headlines that indicate where something needs to be added or designed. I will be happy to give more detail if needed.

Things I still need to get to you in order to design the website;

-Demo video
-Full length public speaking video

Target Market(s)

Corporations, universities, trade associations, private events

Coding

Coded - Design and coding required

Requirements
Must have
• Pictures, links, downloadable forms, MULTIPLE video's embedded, my logo, keep the colors in sync with my existing marketing material
Nice to have
• I would like my design colors thematic as already inherent in my marketing materials (see my Speaker One Sheet)

```html
<!DOCTYPE html>
<html lang="en">
<head>
<meta charset="utf-8">
<title>Brent Halloway — Holistic Lifestyle Hacker</title>
<link href="https://fonts.googleapis.com/css2?family=Roboto+Condensed:ital,wght@0,400;0,700;1,400&family=Open+Sans:ital,wght@0,400;0,600;1,400&display=swap" rel="stylesheet">
<style>
:root{
  --olive:#8c8a55;
  --olive-dark:#4d4f2e;
  --olive-nav:#5a5c36;
  --olive-pale:#e7e8d9;
  --ink:#222;
  --body:#555;
  --grey-bg:#f1f1f1;
  --footer:#1e1e1e;
  --white:#fff;
}
*{box-sizing:border-box;margin:0;padding:0}
html,body{width:1200px;height:3614px;overflow:hidden}
body{font-family:"Open Sans",sans-serif;color:var(--body);background:var(--white);position:relative}
.abs{position:absolute}
section,header,footer,nav{position:absolute;left:0;width:1200px}

/* header */
.topbar{top:0;height:115px;background:var(--white)}
.brand{left:90px;top:26px;display:flex;align-items:center;gap:12px}
.brand-dot{width:58px;height:58px;border-radius:50%;background:var(--olive)}
.brand-name{font-family:"Roboto Condensed",sans-serif;font-weight:700;font-size:32px;color:var(--olive-dark);line-height:1}
.brand-tag{font-family:"Roboto Condensed",sans-serif;font-weight:700;font-size:12px;color:var(--olive-dark);letter-spacing:1px;margin-top:4px}
.social{right:90px;top:40px;display:flex;gap:10px}
.social span{width:26px;height:26px;border-radius:4px;background:#3b6fb0}
.social span:last-child{background:#c33}

.nav{top:115px;height:57px;background:var(--olive-nav);display:flex;justify-content:center;align-items:center;gap:21px}
.nav a{font-family:"Roboto Condensed",sans-serif;color:var(--white);text-decoration:none;font-size:15px;font-weight:700;white-space:nowrap}

/* hero */
.hero{top:172px;height:493px;background:linear-gradient(180deg,#3e3a34 0%,#2d2a26 55%,#54483a 100%);text-align:center;color:var(--white)}
.hero h1{font-family:"Roboto Condensed",sans-serif;font-weight:400;font-size:68px;margin-top:140px}
.hero p{font-family:"Roboto Condensed",sans-serif;font-size:27px;margin-top:12px}
.hero .cta{display:inline-block;margin-top:30px;border:2px solid var(--white);border-radius:22px;padding:8px 24px;font-size:15px;white-space:nowrap}
.hero-dots{right:42px;top:205px;display:flex;flex-direction:column;gap:12px}
.hero-dots i{width:6px;height:6px;border-radius:50%;background:var(--white)}

/* ebook band */
.ebook{top:665px;height:143px;background:var(--olive)}
.book{left:90px;top:-77px;width:166px;height:247px;background:linear-gradient(180deg,#f3e7b0,#e6c86a 60%,#d99c3a);box-shadow:0 2px 6px rgba(0,0,0,.3)}
.avail{left:272px;top:48px;font-family:"Roboto Condensed",sans-serif;font-size:18px;color:var(--white);line-height:24px}
.ebook-quote{left:488px;top:22px;width:560px;font-family:"Roboto Condensed",sans-serif;font-size:17px;color:var(--white);line-height:24px}
.ebook-form{left:488px;top:75px;display:flex}
.ebook-form .field{width:374px;height:46px;background:var(--white);font-size:13px;padding:14px 12px;color:#777}
.ebook-form .btn{width:168px;height:46px;background:var(--olive-dark);color:var(--white);font-family:"Roboto Condensed",sans-serif;font-size:15px;font-weight:700;text-align:center;line-height:46px}

/* intro */
.intro{top:808px;height:352px;text-align:center}
.intro h2{font-family:"Roboto Condensed",sans-serif;font-weight:400;font-size:31px;color:var(--ink);line-height:40px;margin-top:96px}
.downloads{left:145px;top:217px;display:flex;gap:30px}
.downloads div{height:56px;background:var(--white);border:1px solid #ddd;box-shadow:0 2px 5px rgba(0,0,0,.2);font-family:"Roboto Condensed",sans-serif;font-size:15px;color:var(--ink);line-height:56px;text-align:center;white-space:nowrap}

/* stealth */
.stealth{top:1160px;height:293px;background:var(--olive-pale)}
.stealth h2{text-align:center;font-family:"Roboto Condensed",sans-serif;font-weight:400;font-size:29px;color:var(--ink);margin-top:88px}
.stealth ul{list-style:none;position:absolute;top:160px;font-size:18px;color:#444;line-height:50px}
.stealth li::before{content:"» "}

/* about */
.about{top:1453px;height:507px;background:linear-gradient(135deg,#f4f4f4 0%,#ebebeb 50%,#f4f4f4 100%)}
.about h2{left:95px;top:137px;font-family:"Roboto Condensed",sans-serif;font-weight:700;font-size:28px;color:var(--ink)}
.about p{left:95px;top:177px;width:525px;font-size:12.5px;line-height:24px;color:#555}
.video-frame{left:647px;top:77px;width:428px;height:326px;background:var(--olive-dark)}
.video{left:675px;top:102px;width:433px;height:330px;background:linear-gradient(180deg,#8da7c6 0%,#b89a7a 45%,#5a5550 100%)}

/* testimonials */
.testi{top:1960px;height:455px;text-align:center}
.testi h2{font-family:"Roboto Condensed",sans-serif;font-weight:400;font-size:29px;color:var(--ink);margin-top:92px}
.testi blockquote{width:760px;margin:28px auto 0;font-size:14px;line-height:24px;color:#444}
.testi q::before,.testi q::after{color:var(--olive);font-size:20px;font-weight:700}
.avatar{left:552px;top:258px;width:96px;height:96px;border-radius:50%;background:linear-gradient(180deg,#7c8b99,#4b5560)}
.testi .name{left:0;width:1200px;top:360px;font-style:italic;font-size:14px;color:var(--olive)}

/* press */
.press{top:2415px;height:520px;background:var(--grey-bg)}
.press h2{text-align:center;font-family:"Roboto Condensed",sans-serif;font-weight:400;font-size:29px;color:var(--ink);margin-top:68px}
.post{top:145px;width:313px}
.post .pic{height:173px}
.post .tags{display:flex;margin-top:10px;height:22px;font-size:12px}
.post .tags .date{background:var(--olive);color:var(--ink);padding:0 18px;line-height:22px}
.post .tags .cm{background:var(--ink);color:var(--white);padding:0 10px;line-height:22px}
.post h3{font-family:"Open Sans",sans-serif;font-weight:400;font-size:16px;color:var(--ink);margin-top:14px}
.post p{font-size:12px;line-height:17px;color:#666;margin-top:8px}
.post .more{font-size:12px;color:#555;margin-top:7px}

/* clients */
.clients{top:2935px;height:302px;text-align:center}
.clients h2{font-family:"Roboto Condensed",sans-serif;font-weight:400;font-size:29px;color:var(--ink);margin-top:68px}
.client-row{left:120px;top:160px;width:960px;display:flex;justify-content:space-between;align-items:center}
.client-row span{font-family:"Roboto Condensed",sans-serif;font-weight:700;font-size:28px;color:#8a8a8a}

/* banner */
.banner{top:3237px;height:78px;background:var(--olive);color:var(--white);text-align:center;font-family:"Roboto Condensed",sans-serif;font-size:22px;font-weight:700;line-height:78px}

/* footer */
.footer{top:3315px;height:299px;background:var(--footer);color:#ccc}
.f-brand{left:100px;top:60px;width:180px;display:flex;flex-direction:column;align-items:center;gap:6px}
.f-brand .brand-dot{width:66px;height:66px}
.f-brand .brand-name{color:var(--olive);font-size:24px;white-space:nowrap}
.f-brand .brand-tag{color:var(--olive);font-size:10px;white-space:nowrap}
.f-h{font-size:13px;color:#ddd;letter-spacing:.5px}
.contact{left:400px;top:60px}
.contact li{list-style:none;font-size:12px;line-height:18px;margin-top:12px;display:flex;gap:10px}
.contact svg{flex:none;margin-top:2px}
.quick{left:672px;top:60px}
.quick .in{position:absolute;border:1px solid #666;font-size:12px;color:#ddd;padding:4px 6px}
.send{left:1015px;top:172px;width:72px;height:24px;background:var(--olive);color:var(--white);font-size:12px;text-align:center;line-height:24px}
.f-rule{left:100px;top:230px;width:1000px;height:1px;background:#3a3a3a}
.copy{left:100px;top:257px;font-size:12px;color:#ccc}
.f-social{left:1002px;top:255px;display:flex;gap:8px}
.f-social span{width:18px;height:18px;border-radius:3px;background:#ccc}
</style>
</head>
<body>

<header class="topbar">
  <div class="brand abs">
    <span class="brand-dot"></span>
    <div>
      <div class="brand-name">BRENT HALLOWAY</div>
      <div class="brand-tag">YOUR HOLISTIC LIFESTYLE HACKER</div>
    </div>
  </div>
  <div class="social abs" aria-label="Social links"><span></span><span></span><span></span><span></span></div>
</header>

<nav class="nav">
  <a>Home</a><a>About Brent Halloway</a><a>Motivational Speaker/Keynote</a><a>Workshop Presenter</a><a>Author</a><a>Coaching</a><a>Blog</a><a>Online Courses</a><a>Contact Brent Halloway</a>
</nav>

<section class="hero" role="img" aria-label="Open book in front of library shelves">
  <h1>Brent Halloway</h1>
  <p>Sugar Addiction Expert, Holistic Health Expert, Author &amp; Speaker</p>
  <span class="cta">See How Brent Halloway Can Help You or Your Organization</span>
  <div class="hero-dots abs"><i></i><i></i><i></i><i></i></div>
</section>

<section class="ebook">
  <div class="book abs" role="img" aria-label="Book cover"></div>
  <div class="avail abs">Available in Hardback,<br>Paperback and eBook</div>
  <div class="ebook-quote abs">"LEARN WHY EXCUSE MAKING COMES FROM AN IMBALANCED BODY, MIND, AND SOUL, AND WHAT TO DO ABOUT IT!"</div>
  <div class="ebook-form abs"><div class="field">Email Address</div><div class="btn">GET MY FREE E-BOOK</div></div>
</section>

<section class="intro">
  <h2>Your Holistic Lifestyle Hacker<br>Lose Your Mind &amp; Find Your Health!</h2>
  <div class="downloads abs">
    <div style="width:268px">Download Brent's Speaker One Sheet</div>
    <div style="width:268px">Download Brent's Media Sheet</div>
    <div style="width:317px">Download Brent's College Speaker One Sheet</div>
  </div>
</section>

<section class="stealth">
  <h2>Sugar Addiction (The Stealth Addiction) is destroying</h2>
  <ul style="left:283px"><li>Your bottom-line</li><li>The health of your employees</li></ul>
  <ul style="left:665px"><li>Your Insurance Premiums</li><li>The culture of your company</li></ul>
</section>

<section class="about">
  <h2 class="abs">WITHOUT YOUR KNOWLEDGE OR CONSENT!</h2>
  <p class="abs">For over 17 years, Brent Halloway has tirelessly helped executives, employees, and everyday people achieve lasting health and fitness by helping them "lose their minds." Using his whole-person coaching approach, speaking platform, and online training courses, Brent has helped hundreds of people shed their limiting beliefs, eat better, shed sugar addiction and transform their bodies and minds. Brent delights in helping people see through the self-deception of being "normal," and he invites his students to discover and accept the extraordinary people they truly are. If you are ready to transform physically, mentally, emotionally, and spiritually, it is time for you to meet Brent Halloway.</p>
  <div class="video-frame abs"></div>
  <div class="video abs" role="img" aria-label="Video still of the speaker standing outdoors on a mountain deck">
    <svg class="abs" style="left:186px;top:135px" width="60" height="60" viewBox="0 0 60 60"><circle cx="30" cy="30" r="28" fill="rgba(0,0,0,.55)" stroke="#fff" stroke-width="2"/><path d="M24 18 L42 30 L24 42Z" fill="#fff"/></svg>
  </div>
</section>

<section class="testi">
  <h2>Testimonials</h2>
  <blockquote><q>It is a long established fact that a reader will be distracted by the readable content of a page when looking at its layout. The point of using Lorem Ipsum is that it has a more-or-less normal distribution of letters, as opposed to using 'Content here, content here', making it look like readable English.</q></blockquote>
  <svg class="abs" style="left:512px;top:290px" width="16" height="28" viewBox="0 0 16 28"><path d="M14 2 L3 14 L14 26" fill="none" stroke="#999" stroke-width="2.5"/></svg>
  <div class="avatar abs" role="img" aria-label="Portrait of a client"></div>
  <svg class="abs" style="left:672px;top:290px" width="16" height="28" viewBox="0 0 16 28"><path d="M2 2 L13 14 L2 26" fill="none" stroke="#999" stroke-width="2.5"/></svg>
  <div class="name abs">Quisquam est qui</div>
</section>

<section class="press">
  <h2>Press</h2>
  <article class="post abs" style="left:90px">
    <div class="pic" role="img" aria-label="Person reading a book" style="background:linear-gradient(135deg,#3a3330,#8a7a68)"></div>
    <div class="tags"><span class="date">Dec 03</span><span class="cm">0</span></div>
    <h3>Neque porro quisquam dolorem</h3>
    <p>It has survived not only five centuries, but also the leap into electronic typesetting.</p>
    <div class="more">Read More »</div>
  </article>
  <article class="post abs" style="left:437px">
    <div class="pic" role="img" aria-label="Woman reading between library shelves" style="background:linear-gradient(135deg,#3c5a78,#b8553e 55%,#6a4a3a)"></div>
    <div class="tags"><span class="date">Dec 03</span><span class="cm">0</span></div>
    <h3>Porro quisquam est qui</h3>
    <p>It has survived not only five centuries, but also the leap into electronic typesetting.</p>
    <div class="more">Read More »</div>
  </article>
  <article class="post abs" style="left:793px">
    <div class="pic" role="img" aria-label="Open book held on a lap" style="background:linear-gradient(135deg,#c9a98a,#e8ddd0 50%,#5a6d8a)"></div>
    <div class="tags"><span class="date">Dec 03</span><span class="cm">0</span></div>
    <h3>Dolorem ipsum quia dolor</h3>
    <p>It has survived not only five centuries, but also the leap into electronic typesetting.</p>
    <div class="more">Read More »</div>
  </article>
</section>

<section class="clients">
  <h2>Client List</h2>
  <div class="client-row abs">
    <span>RIDGEWAY</span><span>Aurelan</span><span>CONSULATE</span><span>Peridot</span><span>verdant</span><span>FOUNDRY</span>
  </div>
</section>

<section class="banner">Become a Holistic Health Hacker and receive a FREE 30-Day Meal Plan crafted by Brent!</section>

<footer class="footer">
  <div class="f-brand abs">
    <span class="brand-dot"></span>
    <div class="brand-name">BRENT HALLOWAY</div>
    <div class="brand-tag">YOUR HOLISTIC LIFESTYLE HACKER</div>
  </div>
  <div class="contact abs">
    <div class="f-h">CONTACT US</div>
    <ul>
      <li><svg width="10" height="12" viewBox="0 0 10 12"><path d="M5 0a4 4 0 0 1 4 4c0 3-4 8-4 8S1 7 1 4a4 4 0 0 1 4-4z" fill="#ccc"/></svg><span>48 Cedar Hollow Rd. Ste. 12<br>Lakemont, CA 95510</span></li>
      <li><svg width="10" height="12" viewBox="0 0 10 12"><path d="M2 0h2l1 3-1.5 1a6 6 0 0 0 3 3L8 5.5l2 1V9a2 2 0 0 1-2 2C4 11 0 7 0 2a2 2 0 0 1 2-2z" fill="#ccc"/></svg><span>+1-555-0142</span></li>
      <li><svg width="12" height="10" viewBox="0 0 12 10"><rect width="12" height="10" fill="#ccc"/><path d="M0 0l6 5 6-5" fill="none" stroke="#1e1e1e"/></svg><span>hello@bhalloway.example</span></li>
    </ul>
  </div>
  <div class="quick abs">
    <div class="f-h">QUICK FORM</div>
    <div class="in" style="left:0;top:30px;width:204px;height:28px">Name</div>
    <div class="in" style="left:0;top:66px;width:204px;height:28px">Email address</div>
    <div class="in" style="left:214px;top:30px;width:203px;height:64px">Message</div>
  </div>
  <div class="send abs">SEND</div>
  <div class="f-rule abs"></div>
  <div class="copy abs">Copyright © 2017 All Rights Reserved</div>
  <div class="f-social abs"><span></span><span></span><span></span><span></span></div>
</footer>

</body>
</html>
```